Wordpress website design for a Herbal Health Care Company

** Outcome of this project is only the design. Only PSD files of the design for unique pages are sufficient.
** There are a number of unique pages in the new site as shown in the wire-frame. However, for the selection of the designer, Homepage, one 2nd tier page (product category) and one 3rd tier page (product page) is sufficient.
We need web design for our for Ayurvedic & Herbal Products Company located in Sri Lanka
Please get the idea about our company by reading the following text
Vision : To be a world class manufacturer and a supplier of highest quality Ayurvedic pharmaceuticals, Herbal health care products, Herbal cosmetics, Essential oils and Oleoresins
Mission : To provide safe and effective Ayurvedic pharmaceuticals, Herbal health care products and Herbal cosmetics, that is of highest quality and integrity, through the incorporation of ancient ayurvedic wisdom with modern technology and scientific management systems for the inprovement of health and longevity of the people.
Policy on Quality : To design, develop, produce and deliver safe, efficacious and consistent quality Herbal health care products based on Ancient Ayurvedic Wisdom using environmentally preferred process technologies and competent personnel towards continual commitment to total customer satisfaction.
(1) Color theme of the website
You can use the color derived from the company logo
(2) Site Map and description of the site
(1) Home
see the wire frame
http://clipmora.net/t/qWxPlKmR4s7T
we need drop-down menu for top menu bar
(2) About Fern Vale [ This is single page with some description + imaged and following sub page links should be placed in this page]
2.1 Board of Directors
2.2 Milestones
2.3 Our Logo
2.4 Production & R&D
2.5 Certification and Awards
2.6 Global Presence
2.7 Investors
2.8 Distribution
(3)Ayurveda Pharmaceuticals [ This is one of the 3 main categories ,Category Main Page should provide an introduction to the category]
Following shows the sub categories of the “Ayurvedic Pharmaceuticals” . each subcategory has different products. We need unique design for Main Category Page and Sub category
3.1 Arista
3.2 Asava
3.3 Coorna
3.4 Lepa
3.5 Gritha
3.7 Guggulu
3.8 Kalka
3.9 Kwatha
3.10 Pana
see the wireframe
http://clipmora.net/t/7KrtVm83BQNN
when you click subcategory , we nee a page like this to list products
http://clipmora.net/t/HXwQ5nDe21
(4) Herbal Health Care Products [ This is one of the 3 main categories]
you do not find subcategories, you have only products listed. we need unique design for this category page + products
This page will consists of category description with image and products listed
see the wire frame
(5) Cosmetics & Spa Products
see the wire frame
(6) Essential Oils & Oleoresins
see the wire frame
(7) Media
We need to put video / image gallery / text . and future events
(8) Investors
related information to investors
we need image + text
(9) CSR
(10) Contact US
contact us form / address / telephone number and google map
(11) Log In
Normal login form
(12) Career
Reference Details
http://clipmora.net/t/9PeLcR4TYJ
http://clipmora.net/t/5MgkDRR2Vu
http://clipmora.net/t/bNqVrTHww
Here is a similar site that should give you some idea how we like the new site to look http://www.velkor.com
Industry/Entity Type
Health Care
Requirements
Must have
- We have 4 main categories in our production line
Quality Ayurvedic pharmaceuticals, Herbal health care products, Herbal cosmetics, Essential oils and Oleoresins
You can use 4 boxes below the slider for it ( This very important to have unique different design for each category with some heading, text and images etc)
Nice to have
- You can suggest any good nice features. Try to keep a clean, natural, relaxing theme, with shades of green, white and orange as per their logo. This can be seen from the project brief attachments. www.velkor.com is an example.
Should not have
- Please avoid dark colours (red) and sad colours (grey, black)

```html
<!DOCTYPE html>
<html lang="en">
<head>
<meta charset="utf-8">
<title>Fern Vale – Herbal Health Care</title>
<link href="https://fonts.googleapis.com/css2?family=Ubuntu:wght@400;500;700&family=Arimo:wght@400;700&display=swap" rel="stylesheet">
<style>
:root{
  --bg-dark:#262626;
  --bg-mid:#4a4a4a;
  --leaf:#0e7a3c;
  --leaf-deep:#0a5c2c;
  --lime:#c8e01e;
  --lime-soft:#e6f4b8;
  --lime-pale:#f3f9e2;
  --menu-active:#3a4a10;
  --line:#cfe3a0;
  --white:#ffffff;
  --grey-text:#6f6f6f;
}
*{box-sizing:border-box;margin:0;padding:0}
html,body{width:1009px;height:1200px;overflow:hidden}
body{
  position:relative;
  background:radial-gradient(ellipse at 50% 0%, #6a6a6a 0%, var(--bg-mid) 22%, var(--bg-dark) 60%);
  font-family:"Arimo",Arial,sans-serif;
  color:var(--leaf-deep);
}
.abs{position:absolute}

/* header */
.utility-nav{left:540px;top:14px;width:360px;text-align:right;font-size:12px;color:#fff;letter-spacing:.2px}
.utility-nav span{margin:0 7px}
.brand{left:109px;top:0;width:98px;height:93px;background:linear-gradient(#fff,#eef7d8);border-radius:0 0 8px 8px;display:flex;align-items:center;justify-content:center;gap:5px;box-shadow:0 2px 6px rgba(0,0,0,.4)}
.brand-mark{width:8px;height:8px;background:var(--leaf)}
.brand-name{font-family:"Ubuntu",sans-serif;font-weight:500;font-size:15px;color:var(--leaf)}
.search-field{left:629px;top:62px;width:234px;height:21px;border-radius:11px;background:linear-gradient(#fff,#e8e8e8);box-shadow:inset 0 1px 3px rgba(0,0,0,.3)}
.search-btn{left:868px;top:55px;width:30px;height:30px}

/* navigation */
.main-nav{left:86px;top:122px;width:836px;height:36px;background:linear-gradient(#f7fbe9,#e4f2c2);border-radius:6px 6px 0 0;display:flex;align-items:center;padding-left:17px;font-family:"Ubuntu",sans-serif;font-size:13.3px;color:var(--leaf)}
.main-nav a{color:inherit;text-decoration:none;padding:0 5px;height:36px;line-height:36px;white-space:nowrap}
.main-nav a.is-active{background:var(--lime);color:#fff;border-top:3px solid #f08a1c;line-height:30px}

/* page panel */
.page{left:97px;top:158px;width:815px;height:750px;background:#fff}
.slider{left:118px;top:167px;width:670px;height:230px;background:linear-gradient(160deg,#6d7a4a 0%,#d8d8d0 40%,#8a6a40 75%,#4a3a20 100%)}
.slider-dots{left:129px;top:385px;width:100px;height:23px;background:#fff;border-radius:0 0 10px 10px;display:flex;align-items:center;justify-content:center;gap:9px;box-shadow:0 2px 4px rgba(0,0,0,.2)}
.slider-dots i{width:8px;height:8px;border-radius:50%;background:#8cc21e}
.slider-herbs{left:704px;top:316px;width:191px;height:113px;background:radial-gradient(ellipse at 60% 60%,#3e8a2a 0%,#7fb84a 45%,rgba(255,255,255,0) 72%)}
.dropdown{left:266px;top:158px;width:163px;height:154px;background:linear-gradient(rgba(160,200,20,.92),rgba(200,230,30,.95));font-family:"Ubuntu",sans-serif;font-size:13px;color:var(--leaf-deep);box-shadow:0 2px 4px rgba(0,0,0,.25)}
.dropdown li{list-style:none;height:31px;line-height:31px;padding-left:10px}
.dropdown li.is-hover{background:var(--menu-active);color:#fff;height:20px;line-height:20px;margin:4px 0 6px}

.category-thumb{top:455px;height:110px;border:3px solid #fff;box-shadow:0 1px 4px rgba(0,0,0,.35)}
.t1{left:147px;width:149px;background:linear-gradient(135deg,#e6e6e0,#b8c48a 60%,#4f8f2a)}
.t2{left:333px;width:149px;background:linear-gradient(135deg,#8a5a2a,#c89a4a 50%,#5a3018)}
.t3{left:521px;width:148px;background:linear-gradient(135deg,#c8e06a,#7ab83a 50%,#b8dc60)}
.t4{left:707px;width:146px;background:linear-gradient(135deg,#a89a40,#e8e8e0 50%,#6a8a3a)}

/* content boxes */
.about{left:109px;top:600px;width:444px;height:278px;border:1px solid #e3ecd2;padding:8px 10px}
.box-title{font-size:11.5px;color:#222;padding-bottom:6px;border-bottom:1px solid var(--line);margin-bottom:12px}
.about p{font-size:11.4px;line-height:14px;color:var(--leaf);margin-bottom:14px;letter-spacing:.1px}
.side-box{background:linear-gradient(#fff 30%,var(--lime-pale));border-radius:10px;box-shadow:0 1px 4px rgba(0,0,0,.3);padding:8px 11px}
.subscribe{left:579px;top:599px;width:316px;height:78px}
.email-field{position:absolute;left:11px;top:38px;width:234px;height:25px;border:1px solid #d5e3b5;background:#fff;font-size:11.5px;font-style:italic;color:#aaa;padding:5px 7px}
.submit{position:absolute;left:252px;top:42px;font-family:"Ubuntu",sans-serif;font-weight:700;font-size:14px;color:var(--leaf)}
.testimonials{left:579px;top:690px;width:316px;height:138px}
.avatar{position:absolute;width:41px;height:41px;background:#fff;border:1px solid #ccc;border-radius:7px}
.quote{position:absolute;height:40px;background:var(--lime);border:1px solid #9fb318;font-size:11px;font-style:italic;color:#5a6a10;display:flex;align-items:center;justify-content:center}
.blog{left:579px;top:843px;width:316px;height:38px;border-radius:10px;background:linear-gradient(#fff,#e8f4cc);box-shadow:0 1px 4px rgba(0,0,0,.3);text-align:center;line-height:38px;font-family:"Ubuntu",sans-serif;font-weight:500;font-size:14px;color:#2a8a6a}

/* product band */
.product-band{left:97px;top:908px;width:815px;height:187px;background:linear-gradient(#2a2a2a,#3a3a3a)}
.product{bottom:0;background:linear-gradient(#2aa24a,#0e6a2a);border-radius:5px 5px 3px 3px}
.product-label{left:161px;top:1071px;width:95px;height:16px;background:#8a9a70;border-radius:3px;font-size:10.5px;color:#222;text-align:center;line-height:16px}
.band-arrow{top:988px;width:24px;height:22px}

/* footer */
.footer{left:115px;top:1095px;width:780px;height:105px;background:linear-gradient(#fff,var(--lime-soft));border-radius:8px 8px 0 0}
.footer-title{font-size:11.5px;color:#222;padding-bottom:6px;border-bottom:1px solid var(--line)}
.feed{font-size:9.5px;color:var(--grey-text);letter-spacing:.3px}
.contact{font-size:9.5px;color:var(--grey-text);line-height:12.5px;letter-spacing:.2px}
.contact dt{position:absolute;left:0}
.contact dd{margin-left:76px}
.social-badge{left:138px;top:1124px;width:55px;height:50px;background:#dfeefa;border-radius:6px}
.corner-plant{left:0;top:1090px;width:115px;height:110px;background:radial-gradient(ellipse at 50% 60%,#3f8a2a,#1f5a1a 55%,rgba(0,0,0,0) 75%)}
.corner-leaves{left:895px;top:1090px;width:60px;height:110px;background:radial-gradient(ellipse at 20% 60%,#3f9a2a,rgba(0,0,0,0) 70%)}
</style>
</head>
<body>

<nav class="abs utility-nav">Media<span>|</span>Investors<span>|</span>Careers<span>|</span>CSR<span>|</span>Contact us<span>|</span>Log in</nav>

<div class="abs brand"><span class="brand-mark"></span><span class="brand-name">Fern Vale</span></div>

<div class="abs search-field"></div>
<svg class="abs search-btn" viewBox="0 0 30 30" aria-label="Search">
  <circle cx="15" cy="15" r="14" fill="#7cc23a" stroke="#d8f0b0" stroke-width="1.5"/>
  <circle cx="13" cy="13" r="5.5" fill="none" stroke="#fff" stroke-width="2.2"/>
  <line x1="17" y1="17" x2="22" y2="22" stroke="#fff" stroke-width="3" stroke-linecap="round"/>
</svg>

<nav class="abs main-nav">
  <a>Home</a><a>About Fern Vale</a><a class="is-active">Ayurveda Pharmaceuticals</a><a>Herbal Health Care Products</a><a>Cosmetics Spa Products</a><a>Essential Oil &amp; Cleansers</a>
</nav>

<div class="abs page"></div>

<div class="abs slider" role="img" aria-label="Photo of dried herbs and flower petals in white ceramic bowls"></div>
<div class="abs slider-dots"><i></i><i></i><i></i><i></i><i></i></div>
<div class="abs slider-herbs" role="img" aria-label="Illustration of fresh leaves, a mortar and black peppercorns"></div>

<ul class="abs dropdown">
  <li>Menu item 01</li><li>Menu item 01</li><li class="is-hover">Menu item 01</li><li>Menu item 01</li><li>Menu item 01</li>
</ul>

<div class="abs category-thumb t1" role="img" aria-label="Photo of herbal capsules on a green leaf"></div>
<div class="abs category-thumb t2" role="img" aria-label="Photo of heaped spices and star anise"></div>
<div class="abs category-thumb t3" role="img" aria-label="Photo of fresh herb sprigs in a green bowl"></div>
<div class="abs category-thumb t4" role="img" aria-label="Photo of a marble mortar with oil and herbs"></div>

<section class="abs about">
  <h2 class="box-title" style="font-weight:400">About Fern Vale</h2>
  <p>Lorem ipsum dolor sit amet, consectetur adipisicing elit, sed do eiusmod tempor incididunt ut labore et dolore magna aliqua. Ut enim ad minim veniam, quis nostrud exercitation ullamco laboris nisi ut aliquip ex ea commodo consequat. Duis aute irure dolor in reprehenderit in voluptate velit esse cillum dolore eu fugiat nulla pariatur. Excepteur sint occaecat cupidatat non proident, sunt in culpa qui officia deserunt mollit anim id est laborum.</p>
  <p>Lorem ipsum dolor sit amet, consectetur adipisicing elit, sed do eiusmod tempor incididunt ut labore et dolore magna aliqua. Ut enim ad minim veniam, quis nostrud exercitation ullamco laboris nisi ut aliquip ex ea commodo consequat. Duis aute irure dolor in reprehenderit in voluptate velit esse cillum dolore eu fugiat nulla pariatur. Excepteur sint occaecat cupidatat non proident, sunt in culpa qui officia deserunt mollit anim id est laborum.</p>
</section>

<section class="abs side-box subscribe">
  <h2 class="box-title" style="font-weight:400">Subscribe Via Email</h2>
  <div class="email-field">Your Email</div>
  <div class="submit">SUBMIT</div>
</section>

<section class="abs side-box testimonials">
  <h2 class="box-title" style="font-weight:400">Testimonials</h2>
  <div class="avatar" style="left:13px;top:36px"></div>
  <div class="quote" style="left:80px;top:36px;width:223px">“Sample text”</div>
  <svg class="abs" style="left:73px;top:50px" width="8" height="12"><polygon points="8,0 0,6 8,12" fill="#c8e01e"/></svg>
  <div class="quote" style="left:12px;top:86px;width:223px">“Sample text”</div>
  <svg class="abs" style="left:235px;top:100px" width="8" height="12"><polygon points="0,0 8,6 0,12" fill="#c8e01e"/></svg>
  <div class="avatar" style="left:262px;top:86px"></div>
</section>

<div class="abs blog">FERN VALE BLOG</div>

<section class="abs product-band"></section>
<svg class="abs band-arrow" style="left:111px" viewBox="0 0 24 22"><polygon points="0,11 12,1 12,7 24,7 24,15 12,15 12,21" fill="#fff"/></svg>
<svg class="abs band-arrow" style="left:875px" viewBox="0 0 24 22"><polygon points="24,11 12,1 12,7 0,7 0,15 12,15 12,21" fill="#fff"/></svg>

<div class="abs product" style="left:188px;top:923px;width:40px;height:140px" role="img" aria-label="Product photo: green hair oil bottle"></div>
<div class="abs product" style="left:311px;top:1000px;width:47px;height:62px;background:linear-gradient(#3aa84a,#8a2a2a 50%,#2a8a3a)" role="img" aria-label="Product photo: herbal powder box"></div>
<div class="abs product" style="left:433px;top:1007px;width:38px;height:55px;background:linear-gradient(#1e8a3a,#e8f0e0 40%,#1e8a3a)" role="img" aria-label="Product photo: herbal balm jar"></div>
<div class="abs product" style="left:543px;top:923px;width:40px;height:140px" role="img" aria-label="Product photo: green hair oil bottle"></div>
<div class="abs product" style="left:667px;top:1000px;width:47px;height:62px;background:linear-gradient(#3aa84a,#8a2a2a 50%,#2a8a3a)" role="img" aria-label="Product photo: herbal powder box"></div>
<div class="abs product" style="left:789px;top:1007px;width:38px;height:55px;background:linear-gradient(#1e8a3a,#e8f0e0 40%,#1e8a3a)" role="img" aria-label="Product photo: herbal balm jar"></div>
<div class="abs product-label">Product name</div>

<div class="abs corner-plant" role="img" aria-label="Illustration of a mortar with herbs and leaves"></div>
<div class="abs corner-leaves" role="img" aria-label="Illustration of green leaves"></div>

<footer class="abs footer"></footer>
<div class="abs social-badge"></div>
<div class="abs" style="left:209px;top:1101px;width:266px">
  <h3 class="footer-title" style="font-weight:400">Chirpline Feeds</h3>
  <p class="feed" style="margin-top:12px;padding-bottom:14px;border-bottom:1px solid #e3eecb">Chirpline Feed 01</p>
  <p class="feed" style="margin-top:13px">Chirpline Feed 02</p>
</div>
<svg class="abs" style="left:518px;top:1128px" width="38" height="38" viewBox="0 0 38 38" aria-label="Phone">
  <circle cx="19" cy="19" r="18" fill="#f4f8ee" stroke="#cfd8c4"/>
  <path d="M11 12c2-2 4-1 5 1l1 3c0 1-1 2-2 2 1 3 3 5 6 6 0-1 1-2 2-2l3 1c2 1 3 3 1 5-3 3-9 0-12-3s-6-9-4-13z" fill="#4aa83a"/>
</svg>
<div class="abs" style="left:579px;top:1101px;width:316px">
  <h3 class="footer-title" style="font-weight:400">Contact Details</h3>
  <dl class="contact" style="position:relative;margin-top:6px">
    <dt>Address:</dt><dd>42, Palm Grove Lane,<br>Harbour 05<br>Lotus Isle</dd>
    <dt>E-mail:</dt><dd>hello@fernvaleherbals.com</dd>
    <dt>Telephone:</dt><dd>(+00 21) 5550184/ 5550297</dd>
  </dl>
</div>

</body>
</html>
```